New Business Card Design Project

We require a business card design for Vexalund, a newly established Indian company.
Our focus is on the development, manufacturing, and export of a diverse array of pharmaceutical products on a global scale. The card should convey a professional appearance, as our primary markets are in Africa, China, and Southeast Asian nations.
We envision a two-sided business card, with the reverse side dedicated to a logo set against a solid color or an elegantly designed pattern. The corners should be rounded. We would appreciate seeing both horizontal and vertical design options. We trust the designer to utilize their expertise in creating this design.

The content for the business card is included in the attached Word file.

Target Market(s)

Our primary markets are in Africa, China, and Southeast Asian, Latin America, Maldives, Sri Lanka

Industry/Entity Type

Pharmaceutical Manufacturing and Export

Contact Information for Business Card

Colors

Designer to choose colors to be used in the design.

Requirements
Must have
• The reverse side of the business card features solely the logo along with the tagline, "Healing Made Simple."
Should not have
• The logo should not exceed two instances, encompassing both the front and back sides of the card.

```html
<!DOCTYPE html>
<html lang="en">
<head>
<meta charset="utf-8">
<title>Vexalund — Business Card</title>
<link href="https://fonts.googleapis.com/css2?family=Open+Sans:wght@400;600;700&display=swap" rel="stylesheet">
<style>
  :root {
    --backdrop: #232323;
    --card: #1c1d20;
    --blue: #2aa3de;
    --coral: #ef5f4b;
    --text-light: #d9d9d9;
    --text-white: #ffffff;
  }
  * { box-sizing: border-box; margin: 0; padding: 0; }
  html, body {
    width: 1200px;
    height: 780px;
    overflow: hidden;
    background: var(--backdrop);
    font-family: "Open Sans", Arial, sans-serif;
  }
  .sheet {
    position: relative;
    width: 1200px;
    height: 780px;
    display: flex;
    align-items: center;
    justify-content: center;
    gap: 40px;
  }
  .card {
    position: relative;
    width: 540px;
    height: 309px;
    background: var(--card);
    border-radius: 18px;
    overflow: hidden;
  }

  /* Shared brand name */
  .brand {
    display: flex;
    align-items: center;
    gap: 8px;
    color: var(--blue);
    font-weight: 700;
    letter-spacing: 0.5px;
  }
  .brand-dot {
    flex: none;
    border-radius: 50%;
    background: var(--coral);
  }

  /* Front side */
  .front .brand {
    position: absolute;
    left: 38px;
    top: 34px;
    font-size: 34px;
    line-height: 1;
  }
  .front .brand-dot { width: 14px; height: 14px; }

  .address {
    position: absolute;
    left: 40px;
    top: 96px;
    color: var(--text-light);
    font-size: 12px;
    line-height: 17px;
  }
  .contact-list {
    position: absolute;
    left: 40px;
    top: 140px;
    list-style: none;
    color: var(--text-light);
    font-size: 12px;
  }
  .contact-list li {
    display: flex;
    align-items: center;
    gap: 8px;
    height: 20px;
  }
  .contact-list svg { width: 12px; height: 12px; flex: none; }

  .person {
    position: absolute;
    right: 40px;
    top: 196px;
    text-align: right;
  }
  .person-name {
    font-size: 22px;
    line-height: 1.1;
    letter-spacing: 0.4px;
  }
  .person-first { color: var(--blue); font-weight: 700; }
  .person-rest { color: var(--coral); font-weight: 400; }
  .person-role {
    margin-top: 4px;
    color: var(--text-white);
    font-size: 13px;
    letter-spacing: 0.5px;
  }
  .edge-tab {
    position: absolute;
    right: 0;
    top: 230px;
    width: 26px;
    height: 40px;
  }

  /* Back side */
  .back {
    display: flex;
    flex-direction: column;
    align-items: center;
    justify-content: center;
  }
  .back .brand {
    font-size: 60px;
    line-height: 1;
    gap: 12px;
  }
  .back .brand-dot { width: 22px; height: 22px; }
  .tagline {
    align-self: center;
    margin-top: 14px;
    margin-right: 130px;
    color: var(--text-white);
    font-size: 13px;
    letter-spacing: 0.3px;
  }
</style>
</head>
<body>
<main class="sheet">

  <section class="card front" aria-label="Card front">
    <div class="brand">Vexalund<span class="brand-dot"></span></div>

    <p class="address">12, Sundar Nagar,<br>Wardhen, 441204, India</p>

    <ul class="contact-list">
      <li>
        <svg viewBox="0 0 12 12" aria-hidden="true"><rect x="3" y="0.8" width="6" height="10.4" rx="1" fill="none" stroke="var(--coral)" stroke-width="1.2"/></svg>
        +919 530318472
      </li>
      <li>
        <svg viewBox="0 0 12 12" aria-hidden="true"><circle cx="6" cy="6" r="5.2" fill="none" stroke="var(--blue)" stroke-width="1.2"/><ellipse cx="6" cy="6" rx="2.2" ry="5.2" fill="none" stroke="var(--blue)" stroke-width="1"/><line x1="0.8" y1="6" x2="11.2" y2="6" stroke="var(--blue)" stroke-width="1"/></svg>
        www.vexalund.com
      </li>
      <li>
        <svg viewBox="0 0 12 12" aria-hidden="true"><rect x="0.8" y="2.4" width="10.4" height="7.2" rx="1" fill="none" stroke="var(--coral)" stroke-width="1.2"/><polyline points="1,3 6,7 11,3" fill="none" stroke="var(--coral)" stroke-width="1.1"/></svg>
        rtamhane@vexalund.com
      </li>
    </ul>

    <div class="person">
      <p class="person-name"><span class="person-first">Ravik</span> <span class="person-rest">S. Tamhane</span></p>
      <p class="person-role">CEO</p>
    </div>

    <svg class="edge-tab" viewBox="0 0 26 40" aria-hidden="true">
      <rect x="0" y="0" width="26" height="28" fill="var(--blue)"/>
      <rect x="10" y="28" width="16" height="12" fill="var(--blue)"/>
    </svg>
  </section>

  <section class="card back" aria-label="Card back">
    <div class="brand">Vexalund<span class="brand-dot"></span></div>
    <p class="tagline">Healing Made Simple.</p>
  </section>

</main>
</body>
</html>
```